Heron Haulage needs Bussiness cards!

Our new trucking company needs business cards!
We need the same design with two different names and emails, everything else it's the same.
I have included our original logo so we can use it for the design.
Note: the logo to be used is the o e with the buffalo on the right side, next to the letters H and H.

Target Market(s)

Trucking, refrigerated transportation, freight

Industry/Entity Type

Business

Contact Information for Business Card

Card #1:
Marcus Whitfield
marcuswhitfield@heronhaulage.example
1-855-317-6094
(956)238-7160
4117 W. Larkin Ave.
Pharr, TX 78590
www.heronhaulage.example

Card#2:
Rosalba Quintero
rosalba@heronhaulage.example
1-855-317-6094
(956)238-7160
4117 W. Larkin Ave.
Pharr, TX 78590
www.heronhaulage.example

Font styles to use
Sans Serif

Colors
0655a3
ec1f27
ffffff

Requirements
Must have
• our logo
Nice to have
• roads on background,

```html
<!DOCTYPE html>
<html lang="en">
<head>
<meta charset="utf-8">
<title>Heron Haulage – Business Cards</title>
<link href="https://fonts.googleapis.com/css2?family=Source+Sans+3:wght@400;600;700&display=swap" rel="stylesheet">
<style>
  :root {
    --brand-red: #be1e2d;
    --brand-navy: #1c3767;
    --card-white: #ffffff;
    --ghost-grey: #efefef;
    --stage: #e9e9eb;
    --ink: #1c3767;
  }
  * { box-sizing: border-box; margin: 0; padding: 0; }
  html, body {
    width: 1200px;
    height: 844px;
    overflow: hidden;
    background: var(--stage);
    font-family: "Source Sans 3", sans-serif;
  }
  .card {
    position: absolute;
    top: 272px;
    width: 525px;
    height: 300px;
    background: var(--card-white);
    overflow: hidden;
    box-shadow: 0 2px 10px rgba(0,0,0,0.12);
  }

  /* Contact side */
  .card--contact { left: 55px; }
  .band { position: absolute; left: 0; width: 100%; height: 14px; }
  .band--top { top: 0; background: var(--brand-red); }
  .band--bottom { bottom: 0; background: var(--brand-navy); }
  .ghost-mark {
    position: absolute;
    left: -30px;
    top: 40px;
    width: 230px;
    height: 240px;
    border-radius: 48% 52% 40% 60%;
    background: var(--ghost-grey);
  }
  .contact {
    position: absolute;
    left: 170px;
    top: 52px;
    width: 300px;
    text-align: center;
    color: var(--ink);
    font-size: 14.5px;
    line-height: 1.42;
  }
  .contact__name {
    font-size: 20px;
    font-weight: 600;
    margin-bottom: 14px;
  }
  .contact__name .surname { color: var(--brand-red); }
  .contact__address { margin-top: 14px; }

  /* Logo side */
  .card--logo { left: 620px; }
  .tab { position: absolute; width: 26px; height: 50px; }
  .tab--red { left: 0; top: 135px; background: var(--brand-red); }
  .tab--navy { right: 0; top: 38px; background: var(--brand-navy); }
  .wordmark {
    position: absolute;
    left: 0;
    top: 100px;
    width: 100%;
    display: flex;
    align-items: center;
    justify-content: center;
    gap: 12px;
  }
  .wordmark__dot {
    width: 22px;
    height: 22px;
    border-radius: 50%;
    background: var(--brand-red);
  }
  .wordmark__name {
    font-size: 42px;
    font-weight: 700;
    color: var(--brand-navy);
    line-height: 1;
  }
  .website {
    position: absolute;
    left: 0;
    top: 182px;
    width: 100%;
    text-align: center;
    color: var(--brand-red);
    font-size: 14px;
    font-weight: 600;
  }
</style>
</head>
<body>

  <section class="card card--contact">
    <div class="band band--top"></div>
    <div class="ghost-mark" role="img" aria-label="Faint oversized company emblem decoration"></div>
    <div class="contact">
      <p class="contact__name">Marcus <span class="surname">Whitfield</span></p>
      <p>1-855-317-6094</p>
      <p>(956)238-7160</p>
      <p>marcuswhitfield@heronhaulage.example</p>
      <p>www.heronhaulage.example</p>
      <p class="contact__address">4117 W. Larkin Ave. Pharr, TX 78590</p>
    </div>
    <div class="band band--bottom"></div>
  </section>

  <section class="card card--logo">
    <div class="tab tab--red"></div>
    <div class="tab tab--navy"></div>
    <div class="wordmark">
      <span class="wordmark__dot"></span>
      <span class="wordmark__name">Heron Haulage</span>
    </div>
    <p class="website">www.heronhaulage.example</p>
  </section>

</body>
</html>
```